Launching a new real estate agency in Monaco

Hello, I am opening a new real estate agency in Monaco. For the purpose of my activity, in order to be known quickly among a fierce competition I need an advertising campaign that will be broadcast in local magazines, newspapers, paper board, etc.

You will find example of pictures of Monaco on which I have the rights and my logo. You can always pick other images that I can buy if the price is reasonable for a commercial use (<200 $)

Please respect the color code.

I wish you good luck and look forward to give you my feedbacks

Reason: Only few projects posted were respecting the brief and of quality. Hoping to receive more in coming days

Target Market(s)

International high-end clientele of all ages, all genders.

Industry/Entity Type

Real Estate Agent

Font styles to use
Serif

Requirements
Must have
• 1/ My logo
• 2/ This message "Un nouveau regard sur l'immobilier" means in English a fresh look at real estate or new eyes on real-estate.
• 3/ My address: 14 rue des Ormeaux, Galerie Bellerive Nord, 98 000 Monaco
• 4/ Phone number: +377.93.48.25.07
• 5/ Website: www.corvano-immo.com.
• 6/ Format: Files should be easily adjustable but I'd like a vertical display to fit easily in Magazines, Poster and billboard. So please work in high resolution !
Nice to have
• Please think about your design in accordance with the message I want to display.
Should not have
• A simple poster with a picture of Monaco that does not take into consideration the message of the advertisement, "Un nouveau regard sur l'immobilier" which means in english, new eyes on real-estate or a new look at real-estate, or new vision at real-estate.

```html
<!DOCTYPE html>
<html lang="fr">
<head>
<meta charset="utf-8">
<title>Corvano Immo — Un nouveau regard sur l'immobilier</title>
<link rel="stylesheet" href="https://fonts.googleapis.com/css2?family=Patrick+Hand+SC&family=Inter:wght@400;700&family=Quicksand:wght@700&display=swap">
<style>
  :root {
    --band: #2b292e;
    --ink-light: #ffffff;
    --ink-muted: #e6e4e8;
    --ink-dark: #333236;
    --copper: #d99a85;
    --divider: #5c5a60;
  }
  html, body {
    margin: 0;
    padding: 0;
    overflow: hidden;
    background: #ffffff;
  }
  .poster {
    position: relative;
    width: 849px;
    height: 1200px;
    overflow: hidden;
    font-family: "Inter", Arial, sans-serif;
  }
  .top-band {
    position: absolute;
    inset: 0 0 auto 0;
    height: 408px;
    background: var(--band);
  }
  .website {
    position: absolute;
    left: 114px;
    top: 126px;
    margin: 0;
    font-size: 15px;
    color: var(--ink-muted);
  }
  .brand {
    position: absolute;
    left: 438px;
    top: 88px;
    display: flex;
    align-items: center;
    gap: 14px;
    white-space: nowrap;
  }
  .brand-dot {
    width: 34px;
    height: 34px;
    border-radius: 50%;
    background: var(--copper);
  }
  .brand-name {
    font-family: "Quicksand", Arial, sans-serif;
    font-weight: 700;
    font-size: 34px;
    letter-spacing: 2px;
    color: var(--copper);
    text-transform: uppercase;
  }
  .headline {
    position: absolute;
    right: 109px;
    top: 284px;
    margin: 0;
    text-align: right;
    white-space: nowrap;
    font-family: "Patrick Hand SC", "Comic Sans MS", cursive;
    font-weight: 400;
    font-size: 50px;
    line-height: 50px;
    letter-spacing: 1px;
    color: var(--ink-light);
  }
  .divider {
    position: absolute;
    left: 777px;
    top: 264px;
    width: 2px;
    height: 144px;
    background: var(--divider);
  }
  .city-visual {
    position: absolute;
    left: 330px;
    top: 408px;
    width: 519px;
    height: 792px;
    background: linear-gradient(180deg, #f4c56f 0%, #e58b5a 10%, #b66e99 22%, #8a6a9c 45%, #6b4b6e 62%, #8a5a3e 80%, #c7822f 100%);
  }
  .curtain-visual {
    position: absolute;
    left: 0;
    top: 408px;
  }
  .contact {
    position: absolute;
    left: 114px;
    top: 1015px;
    color: var(--ink-dark);
  }
  .address {
    margin: 0;
    font-style: normal;
    font-size: 14px;
    line-height: 19px;
  }
  .phone {
    margin: 8px 0 0;
    font-weight: 700;
    font-size: 19px;
  }
</style>
</head>
<body>
<div class="poster">
  <header class="top-band">
    <p class="website">www.corvano-immo.com</p>
    <div class="brand">
      <span class="brand-dot"></span>
      <span class="brand-name">Corvano Immo</span>
    </div>
    <h1 class="headline">Un nouveau regard<br>sur l'immobilier"</h1>
    <span class="divider"></span>
  </header>

  <div class="city-visual" role="img" aria-label="Aerial view of Monaco's harbour and towers at sunset over the sea"></div>

  <svg class="curtain-visual" width="440" height="792" viewBox="0 0 440 792" role="img" aria-label="A hand drawing back a white curtain to reveal the city view">
    <defs>
      <linearGradient id="curtain-fill" x1="0" y1="0" x2="1" y2="0">
        <stop offset="0" stop-color="#e2e2e2"/>
        <stop offset="0.6" stop-color="#dadada"/>
        <stop offset="0.82" stop-color="#ececec"/>
        <stop offset="1" stop-color="#f7f7f7"/>
      </linearGradient>
    </defs>
    <path d="M0 0 H428 C405 150 360 300 362 420 C364 600 345 700 352 792 H0 Z" fill="url(#curtain-fill)"/>
  </svg>

  <div class="contact">
    <address class="address">14 rue des Ormeaux,<br>Galerie Bellerive Nord,<br>98 000 Monaco</address>
    <p class="phone">Ph.: +377.93.48.25.07</p>
  </div>
</div>
</body>
</html>
```